Commercial Refrigeration Service Company requires stylish and fresh looking flyer.

We need a flyer to hand out to new customers. It should have a photo and our branding, list all the services that are offered and our contact details.
We would like two flyers to be supplied, both identical though one offering a discount until July ( Half Price Service Fee ). The flyer should be clear, interesting and in similar colours to the branding package supplied.
Please look at our website for information about the services on offer:
www.brisko-coolworks.com.au

Target Market(s)

Cafes, bars, restaurants, pubs ect.

Font styles to use
Other font styles liked:
• Font package provided

Colors
85cae6
ffffff
333333

Requirements
Must have
• - The photo provided.
• - The company logo.
• - Similar feel to the website & business card.
• - Smooth layout and clear to understand.
Should not have
• - No clunky badges or prints.

```html
<!DOCTYPE html>
<html lang="en">
<head>
<meta charset="utf-8">
<title>Brisko Commercial Refrigeration – Flyer</title>
<link href="https://fonts.googleapis.com/css2?family=Dosis:wght@400;500&family=Raleway:wght@700;800&family=Questrial&display=swap" rel="stylesheet">
<style>
  :root {
    --brand-blue: #5bc2ea;
    --brand-blue-text: #4fb7e3;
    --ink: #333333;
    --footer-dark: #262828;
    --paper-top: #f7f7f7;
    --paper-bottom: #e6e6e6;
    --stage: #7a7a7a;
    --white: #ffffff;
  }
  * { box-sizing: border-box; margin: 0; padding: 0; }
  html, body { width: 1200px; height: 1146px; overflow: hidden; }
  body { background: var(--stage); position: relative; }

  .flyer {
    position: absolute; left: 208px; top: 18px;
    width: 784px; height: 1110px;
    background: linear-gradient(180deg, var(--paper-top) 40%, var(--paper-bottom) 100%);
    overflow: hidden;
  }
  .hero-photo {
    position: absolute; left: 0; top: 0; width: 100%; height: 294px;
    background: linear-gradient(180deg, #9cc3dd 0%, #c9d9e2 35%, #8a8f96 60%, #6f747a 80%, #9a9a96 100%);
  }
  .brand-band {
    position: absolute; left: 0; top: 294px; width: 100%; height: 158px;
    background: var(--brand-blue);
    display: flex; align-items: center; justify-content: center; gap: 18px;
  }
  .brand-mark {
    width: 22px; height: 22px; border-radius: 50%;
    background: var(--ink);
  }
  .brand-name {
    font-family: "Questrial", sans-serif; font-weight: 400;
    font-size: 52px; line-height: 1; color: var(--ink);
  }
  .company-type {
    position: absolute; left: 0; right: 0; top: 478px; text-align: center;
    font-family: "Questrial", sans-serif; font-size: 24px; line-height: 30px;
    color: var(--ink);
  }
  .offer-box {
    position: absolute; left: 101px; top: 574px; width: 574px; height: 122px;
    border: 1.5px solid var(--brand-blue); text-align: center;
  }
  .offer-title {
    margin-top: 22px;
    font-family: "Dosis", sans-serif; font-weight: 500; font-size: 50px; line-height: 50px;
    color: var(--brand-blue-text);
  }
  .offer-detail {
    margin-top: 2px;
    font-family: "Dosis", sans-serif; font-weight: 400; font-size: 26px; line-height: 30px;
    color: var(--brand-blue-text);
  }
  .services { position: absolute; left: 0; right: 0; top: 742px; text-align: center; }
  .services-heading {
    font-family: "Raleway", sans-serif; font-weight: 800; font-size: 23px; color: var(--ink);
  }
  .services-heading .dots { display: inline-block; vertical-align: middle; margin: 0 6px; }
  .services-heading .dots i {
    display: inline-block; width: 4px; height: 4px; border-radius: 50%;
    background: var(--brand-blue); margin: 0 4px;
  }
  .services-list {
    margin-top: 4px; list-style: none;
    font-family: "Raleway", sans-serif; font-weight: 700; font-size: 20.5px; line-height: 25px;
    color: var(--brand-blue-text);
  }
  .company-details {
    position: absolute; left: 0; right: 0; top: 873px; text-align: center;
    font-family: "Questrial", sans-serif; font-style: normal;
    font-size: 19px; line-height: 23px; color: var(--ink);
  }
  .social-handle {
    position: absolute; left: 0; right: 0; top: 936px; text-align: center;
    font-family: "Questrial", sans-serif; font-size: 17px; color: var(--ink);
  }
  .footer-shape { position: absolute; left: 0; top: 1015px; width: 784px; height: 95px; }
  .footer-contact {
    position: absolute; left: 47px; top: 1026px;
    font-family: "Questrial", sans-serif; font-size: 18.5px; line-height: 23px; color: var(--white);
  }
</style>
</head>
<body>
  <main class="flyer">
    <div class="hero-photo" role="img" aria-label="Photo of the technician standing beside the branded service ute at the beach"></div>

    <header class="brand-band">
      <span class="brand-mark"></span>
      <span class="brand-name">Brisko</span>
    </header>

    <p class="company-type">Commercial Refrigeration</p>

    <section class="offer-box">
      <h2 class="offer-title">DISCOUNT UNTIL JULY</h2>
      <p class="offer-detail">PAY ONLY HALF PRICE OF THE SERVICE FEE</p>
    </section>

    <section class="services">
      <h3 class="services-heading"><span class="dots"><i></i><i></i><i></i></span>OUR SERVICES<span class="dots"><i></i><i></i><i></i></span></h3>
      <ul class="services-list">
        <li>COMMERCIAL REFRIGERATION</li>
        <li>ICE MAKERS | BEER SYSTEMS | ELECTRICAL</li>
        <li>24HR SERVICE | SALES | INSTALLATION</li>
      </ul>
    </section>

    <address class="company-details">
      PO Box 5120 Clovelly Bay NSW 2031<br>
      ABN: 48 702 319 554 | Licence No: 418273C
    </address>

    <p class="social-handle">@briskocoolworks</p>

    <svg class="footer-shape" viewBox="0 0 784 95" aria-hidden="true">
      <polygon points="0,0 320,0 400,72 784,72 784,95 0,95" fill="var(--footer-dark)"/>
    </svg>
    <div class="footer-contact">
      0400 512 880<br>
      info@brisko-coolworks.com.au<br>
      www.brisko-coolworks.com.au
    </div>
  </main>
</body>
</html>
```